Business Card Design

We would like to re-design our business cards. Our Company - Qwinrel Turbochargers, rebuilds turbochargers and sells replacement parts. Our website is: http://www.qwinrelturbochargers-example.com
We just had our logo changed. I will attach the file. Looking for fresh new/modern business card. We like the colors red, black, white and silver. Black background looks attractive, but not a requirement. The final design should communicate reasonable/competitive prices, top quality and reliability of our products.
Updates
Project Deadline Extended
Reason: Need to finalize the info on the card. Currently working on changing address and email info. Want to make sure it is the correct one before accepting the final design. Unless, this is something that can be changed at a later time..??
Industry/Entity Type
Business
Contact Information for Business Card
QWINREL TURBOCHARGERS, LLC
20473 Harwick Lane NE
Massillon, OH 44647
Tel: +1-555-214-7390
Fax: +1-555-267-1842
info@QwinrelTurbochargers-example.com
Our current business card had the following highlights:
*We rebuild all Turbocharges for Automotive, Diesel and Industrial
*Precision Balancing and in-house turbocharger needs
*All Turbocharger replacement parts are made in USA / U.K.
Look and feel
Each slider illustrates characteristics of the customer's brand and the style your logo design should communicate.

```html
<!DOCTYPE html>
<html lang="en">
<head>
<meta charset="utf-8">
<title>Qwinrel Turbochargers – Business Card</title>
<link href="https://fonts.googleapis.com/css2?family=Lato:wght@400;700&display=swap" rel="stylesheet">
<style>
  :root {
    --page: #2b2b2d;
    --card: #1b1b1d;
    --card-edge: #232326;
    --red: #e3262b;
    --white: #f4f4f4;
    --silver: #c9c9cc;
  }
  * { box-sizing: border-box; margin: 0; padding: 0; }
  html, body {
    width: 1200px; height: 900px; overflow: hidden;
    background: var(--page);
    font-family: "Lato", Arial, sans-serif;
  }
  .stage {
    position: relative; width: 1200px; height: 900px;
    display: flex; align-items: center; justify-content: center; gap: 40px;
  }
  .card {
    width: 520px; height: 300px;
    border-radius: 22px;
    background: linear-gradient(150deg, var(--card-edge), var(--card));
    box-shadow: 0 14px 30px rgba(0,0,0,.45);
    position: relative; color: var(--white);
  }
  /* front */
  .card--front { display: flex; align-items: center; padding: 0 26px 0 30px; }
  .brand-block {
    width: 165px; flex: none; display: flex; align-items: center; gap: 10px;
  }
  .brand-dot {
    width: 16px; height: 16px; border-radius: 50%;
    background: var(--red); flex: none;
  }
  .brand-name {
    font-weight: 700; font-size: 21px; line-height: 1.15; color: var(--white);
  }
  .contact { margin-left: 22px; min-width: 0; }
  .contact__name { font-size: 23px; font-weight: 400; }
  .contact__role { font-size: 14.5px; color: var(--red); margin-bottom: 14px; }
  .contact__address { font-size: 14px; line-height: 1.4; margin-bottom: 14px; }
  .contact__line { font-size: 13.5px; line-height: 1.5; white-space: nowrap; }
  .contact__label { color: var(--red); }
  /* back */
  .card--back { padding: 34px 36px; }
  .back-brand { display: flex; align-items: center; gap: 12px; margin-bottom: 26px; justify-content: flex-end; }
  .back-brand .brand-name { font-size: 24px; }
  .highlights { list-style: none; }
  .highlight {
    display: flex; gap: 10px; font-size: 15px; line-height: 1.35;
    margin-bottom: 10px; color: var(--silver);
  }
  .highlight--accent { color: var(--red); }
  .highlight svg { flex: none; margin-top: 5px; }
</style>
</head>
<body>
<main class="stage">
  <section class="card card--front" aria-label="Business card front">
    <div class="brand-block">
      <span class="brand-dot"></span>
      <span class="brand-name">Qwinrel Turbochargers</span>
    </div>
    <div class="contact">
      <p class="contact__name">Daniel Harlow</p>
      <p class="contact__role">Managing Director</p>
      <p class="contact__address">20473 Harwick Lane NE<br>Massillon, OH 44647</p>
      <p class="contact__line"><span class="contact__label">T:</span> +1-555-214-7390</p>
      <p class="contact__line"><span class="contact__label">E:</span> info@QwinrelTurbochargers-example.com</p>
      <p class="contact__line"><span class="contact__label">W:</span> www.qwinrelturbochargers-example.com</p>
    </div>
  </section>

  <section class="card card--back" aria-label="Business card back">
    <div class="back-brand">
      <span class="brand-dot"></span>
      <span class="brand-name">Qwinrel Turbochargers</span>
    </div>
    <ul class="highlights">
      <li class="highlight">
        <svg width="14" height="8" viewBox="0 0 14 8"><path d="M0 8 L14 0 L10 8 Z" fill="#f4f4f4"/></svg>
        <span>We Rebuild all Turbochargers for Automotive, Diesel and Industrial.</span>
      </li>
      <li class="highlight highlight--accent">
        <svg width="14" height="8" viewBox="0 0 14 8"><path d="M0 8 L14 0 L10 8 Z" fill="#f4f4f4"/></svg>
        <span>Precision Balancing And in-House machining for all your custom turbocharger needs.</span>
      </li>
      <li class="highlight">
        <svg width="14" height="8" viewBox="0 0 14 8"><path d="M0 8 L14 0 L10 8 Z" fill="#f4f4f4"/></svg>
        <span>All Turbocharger Replacement parts are made in North America &amp; U.K.</span>
      </li>
    </ul>
  </section>
</main>
</body>
</html>
```